Suds Haven Laundromat Wordpress Design

We need a Wordpress website design for our laundromat, Suds Haven Atlanta, at www.sudshavenatlanta-example.com. We would like to have 6 pages: Home, About Us, Services, Locations, Reviews and Contact us. We will provide content for the text on each page. What we do: We are a full service laundromat that provides dry cleaning drop off, professional laundry services, wash dry fold and self service laundry to the local community. We would like to use the color scheme from our logo to convey a warm, safe, and bright business that caters to its diverse community.
Updates

I like the structure of this laundromat website: http://www.washtroveusa-example.com/ Using my logo and color scheme in the above referenced website is what. Am looking for. The photos attached to the project with the female model should be used as a primary focus and supplemented by actual photos of the equipment.

Target Market(s)

Our target market is a diverse group of people from Midtown Atlanta - LGBTQ community /Locals/Regulars that have been coming to laundromat for 30 years.

Industry/Entity Type

Laundromat

Coding

Coded - Design and coding required

Number of Pages Required

5+ page

Font styles to use
Sans Serif

Colors
0054AA
0677BA
7BADD7
CADEEF
E8F1F8

Requirements
Must have
• Feature this video on the main page: https://videohost-example.com/xq7Rm2bPz4k

```html
<!DOCTYPE html>
<html lang="en">
<head>
<meta charset="utf-8">
<title>About Us – Suds Haven Atlanta</title>
<link rel="stylesheet" href="https://fonts.googleapis.com/css2?family=Montserrat:wght@400;500;600&family=Oswald:wght@500&display=swap">
<style>
:root{
  --blue-deep:#0054aa;
  --blue-mid:#0677ba;
  --blue-bright:#11a3e0;
  --blue-soft:#7badd7;
  --ink:#1e2430;
  --muted-bg:#f1f5f8;
  --card-bg:#e3e8eb;
  --footer-bg:#2f4263;
  --footer-line:#4a5b7a;
  --photo-tone:#b7aea0;
  --white:#ffffff;
}
*{margin:0;padding:0;box-sizing:border-box}
html,body{width:1200px;height:2218px;overflow:hidden;background:var(--white)}
body{position:relative;font-family:"Montserrat",sans-serif;color:var(--ink)}
.abs{position:absolute}

.site-header{position:absolute;left:0;top:0;width:1200px;height:76px;background:var(--white)}
.brand{position:absolute;left:103px;top:22px;font-size:26px;font-weight:600;color:var(--blue-mid);letter-spacing:.5px;display:flex;align-items:center;gap:8px}
.brand .dot{width:12px;height:12px;border-radius:50%;background:var(--blue-mid)}
.main-nav a{position:absolute;top:34px;font-size:12.5px;color:var(--ink);text-decoration:none;letter-spacing:.2px}
.main-nav a.active{font-weight:600}
.nav-underline{position:absolute;left:617px;top:72px;width:68px;height:4px;background:var(--blue-deep)}
.nav-divider{position:absolute;left:1029px;top:20px;width:2px;height:37px;background:var(--blue-deep)}
.social-top{position:absolute;top:35px;font-size:10px;font-weight:600;color:var(--ink)}

.hero{position:absolute;left:0;top:76px;width:1200px;height:604px}

.breadcrumb{position:absolute;left:163px;top:698px;font-size:12.5px}
.breadcrumb span{color:var(--blue-deep);font-weight:600}

.photo{position:absolute;left:179px;top:841px;width:307px;height:307px;border-radius:50%;background:var(--photo-tone)}

.section-title{font-family:"Oswald",sans-serif;font-weight:500;text-transform:uppercase;color:var(--ink)}
.section-title em{font-style:normal;color:var(--blue-deep)}
.about-title{position:absolute;left:573px;top:794px;font-size:30px}
.title-rule{position:absolute;height:3px;width:45px;background:var(--blue-mid)}
.about-text{position:absolute;left:573px;top:857px;width:466px;font-size:13.6px;line-height:27px}
.about-text p+p{margin-top:5px}
.btn{position:absolute;left:572px;top:1089px;width:150px;height:41px;background:var(--blue-bright);color:var(--white);font-size:13px;font-weight:500;display:flex;align-items:center;justify-content:center;border-radius:2px}

.why{position:absolute;left:0;top:1244px;width:1200px;height:449px;background:var(--muted-bg)}
.why-title{position:absolute;left:0;width:1200px;top:73px;text-align:center;font-size:31px}
.card{position:absolute;width:282px;height:104px;background:var(--card-bg);border-radius:4px;padding:20px 18px 0 41px;font-size:13.6px;line-height:24px}
.card svg{position:absolute;left:13px;top:25px}

.site-footer{position:absolute;left:0;top:1693px;width:1200px;height:525px;background:var(--footer-bg);color:var(--white)}
.footer-brand{position:absolute;left:0;width:1200px;top:95px;text-align:center;font-size:40px;font-weight:600;letter-spacing:1px}
.footer-brand small{display:block;font-size:13px;font-weight:500;letter-spacing:.5px;margin-top:2px}
.rule{position:absolute;height:1px;background:var(--footer-line)}
.footer-nav a{position:absolute;top:1925px;font-size:15px;color:var(--white);text-decoration:none}
.social-dot{position:absolute;top:1917px;width:30px;height:30px;border-radius:50%;background:var(--white)}
.info{position:absolute;font-size:13.8px;line-height:24px}
.info.highlight{color:var(--blue-bright)}
.copyright{position:absolute;left:163px;top:2155px;font-size:12px}
.copyright b{font-weight:600}
.pay-mark{position:absolute;left:906px;top:2150px;display:flex;align-items:center;gap:6px;font-size:16px;font-weight:600;color:var(--blue-bright)}
.pay-mark i{width:18px;height:18px;background:var(--blue-bright);display:block}
</style>
</head>
<body>

<header class="site-header">
  <div class="brand"><span class="dot"></span>Suds Haven</div>
  <nav class="main-nav">
    <a style="left:537px">HOME</a>
    <a class="active" style="left:617px">ABOUT US</a>
    <a style="left:725px">SERVICES</a>
    <a style="left:827px">REVIEWS</a>
    <a style="left:925px">CONTACT US</a>
  </nav>
  <div class="nav-underline"></div>
  <div class="nav-divider"></div>
  <span class="social-top" style="left:1042px">Circleside</span>
  <span class="social-top" style="left:1100px">Chirper</span>
</header>

<svg class="hero" viewBox="0 0 1200 604" width="1200" height="604">
  <defs>
    <linearGradient id="heroFill" x1="0" y1="0" x2="0" y2="1">
      <stop offset="0" stop-color="#b9d6d2"/>
      <stop offset=".45" stop-color="#a9adb0"/>
      <stop offset="1" stop-color="#6e7275"/>
    </linearGradient>
  </defs>
  <path d="M0 0H1200V516Q600 690 0 516Z" fill="url(#heroFill)" role="img" aria-label="Photo of a retro laundromat with rows of washers and a woman in a blue dress"/>
  <path d="M0 528Q560 680 1148 536Q560 700 0 540Z" fill="var(--blue-deep)"/>
</svg>

<div class="breadcrumb">HOME / <span>ABOUT US</span></div>

<div class="photo" role="img" aria-label="Round portrait photo of a customer in a knit hat listening to earphones"></div>

<h1 class="section-title about-title">About <em>Us</em></h1>
<div class="title-rule" style="left:573px;top:839px"></div>
<div class="about-text">
  <p>Suds Haven is family-owned laundromat that has been serving Midtown, GA for over 45 years. We are proud to offer high quality and convenient services to the area residents and business owners and strive to keep our customers clothing in tip top shape.</p>
  <p>Whether you have commercial laundry needs, are washing clothes for your family, or want to relax that weekend and have us pick up and wash/dry/fold for you, the professionals at Suds Haven are ready to meet your goals.</p>
</div>
<div class="btn">Contact Us Today</div>

<section class="why">
  <h2 class="section-title why-title">Why <em>Choose Us</em></h2>
  <div class="title-rule" style="left:577px;top:119px"></div>
</section>

<div class="card" style="left:161px;top:1390px"><svg width="17" height="15" viewBox="0 0 17 15"><path d="M13 4A6.5 6.5 0 1 0 14 8" fill="none" stroke="var(--blue-mid)" stroke-width="1.5"/><path d="M4 7L7.5 10.5L16 1" fill="none" stroke="var(--blue-mid)" stroke-width="1.5"/></svg>In Business over 45 years and one of Atlanta's first, finest, and Friendliest coin laundries</div>
<div class="card" style="left:459px;top:1390px"><svg width="17" height="15" viewBox="0 0 17 15"><path d="M13 4A6.5 6.5 0 1 0 14 8" fill="none" stroke="var(--blue-mid)" stroke-width="1.5"/><path d="M4 7L7.5 10.5L16 1" fill="none" stroke="var(--blue-mid)" stroke-width="1.5"/></svg>Voted "BEST COIN LAUNDRY" – Multiple years</div>
<div class="card" style="left:756px;top:1390px"><svg width="17" height="15" viewBox="0 0 17 15"><path d="M13 4A6.5 6.5 0 1 0 14 8" fill="none" stroke="var(--blue-mid)" stroke-width="1.5"/><path d="M4 7L7.5 10.5L16 1" fill="none" stroke="var(--blue-mid)" stroke-width="1.5"/></svg>One of The Best Wash-Dry-Fold</div>
<div class="card" style="left:161px;top:1510px"><svg width="17" height="15" viewBox="0 0 17 15"><path d="M13 4A6.5 6.5 0 1 0 14 8" fill="none" stroke="var(--blue-mid)" stroke-width="1.5"/><path d="M4 7L7.5 10.5L16 1" fill="none" stroke="var(--blue-mid)" stroke-width="1.5"/></svg>Cool – Comfortable – Clean</div>
<div class="card" style="left:459px;top:1510px"><svg width="17" height="15" viewBox="0 0 17 15"><path d="M13 4A6.5 6.5 0 1 0 14 8" fill="none" stroke="var(--blue-mid)" stroke-width="1.5"/><path d="M4 7L7.5 10.5L16 1" fill="none" stroke="var(--blue-mid)" stroke-width="1.5"/></svg>Over 50 Well Maintained Machines</div>
<div class="card" style="left:756px;top:1510px"><svg width="17" height="15" viewBox="0 0 17 15"><path d="M13 4A6.5 6.5 0 1 0 14 8" fill="none" stroke="var(--blue-mid)" stroke-width="1.5"/><path d="M4 7L7.5 10.5L16 1" fill="none" stroke="var(--blue-mid)" stroke-width="1.5"/></svg>Ability to pay via Credit Card with CoinTap app</div>

<footer class="site-footer">
  <div class="footer-brand">SUDS HAVEN<small>A FULL SERVICE LAUNDROMAT</small></div>
</footer>
<div class="rule" style="left:327px;top:1891px;width:543px"></div>
<nav class="footer-nav">
  <a style="left:298px">Home</a>
  <a style="left:392px">About Us</a>
  <a style="left:502px">Services</a>
  <a style="left:606px">Reviews</a>
  <a style="left:708px">Contact Us</a>
</nav>
<span class="social-dot" style="left:825px" role="img" aria-label="Circleside"></span>
<span class="social-dot" style="left:870px" role="img" aria-label="Chirper"></span>
<div class="rule" style="left:327px;top:1973px;width:543px"></div>

<svg class="abs" style="left:246px;top:2000px" width="18" height="20" viewBox="0 0 18 20"><circle cx="9" cy="11" r="7.5" fill="none" stroke="#fff" stroke-width="1.2"/><path d="M9 3.5V18.5M1.5 11H16.5M9 3.5C5 7 5 15 9 18.5M9 3.5C13 7 13 15 9 18.5" fill="none" stroke="#fff" stroke-width="1"/></svg>
<div class="info" style="left:277px;top:1999px;color:#fff">Brightwell Plaza, 2870 Marlow Ave NE.,<br># 112, Atlanta, GA 30399</div>
<svg class="abs" style="left:246px;top:2056px" width="18" height="18" viewBox="0 0 18 18"><path d="M3 1.5L6.5 5L4.8 7.2C6 10 8 12 10.8 13.2L13 11.5L16.5 15L14 17C7 16 2 11 1 4Z" fill="none" stroke="#fff" stroke-width="1.2" stroke-linejoin="round"/></svg>
<div class="info" style="left:275px;top:2053px;color:#fff">(404) 555-0187</div>
<div class="info highlight" style="left:611px;top:1998px">Delivery Available* please contact us for details</div>
<div class="info" style="left:611px;top:2031px;color:#fff">Covid 19 hours - open 7 days a week 8 am to 8 pm<br>Last wash begins 6:30 pm</div>
<div class="rule" style="left:161px;top:2110px;width:877px"></div>
<div class="copyright" style="color:#fff">Copyright © 2021 <b>Suds Haven Atlanta</b>. All Rights Reserved.</div>
<div class="pay-mark"><i></i>CoinTap</div>

</body>
</html>
```